Looking for a modern, Professional business card design

We have a simple business card, but are looking for a more modern, professional look. A sample of the basic card is attached as well as the logo. We would also like to add that we offer:
Struggling with your finances?
- Learn to become debt free
- Discover the power of cash
- Control your money instead of it controlling you
Let us help you achieve a new level of financial freedom!
Also, we would like to have a "SPECIAL OFFER!: FREE 30 minute consultation"
Financial Planning

```html
<!DOCTYPE html>
<html lang="en">
<head>
<meta charset="utf-8">
<title>Steadfast Money Coaching – Business Card</title>
<link href="https://fonts.googleapis.com/css2?family=Arimo:wght@400&family=Libre+Franklin:wght@800&display=swap" rel="stylesheet">
<style>
  :root{
    --backdrop:#d8d4cd;
    --card:#ecebe6;
    --band:#151515;
    --band-edge:#2a2a2a;
    --green:#2f8a1f;
    --green-dark:#1f5f14;
    --green-light:#5fb53a;
    --ink:#1a1a1a;
    --muted:#d7d7d7;
  }
  *{box-sizing:border-box;margin:0;padding:0}
  html,body{width:1200px;height:969px;overflow:hidden}
  body{background:var(--backdrop);display:flex;align-items:center;justify-content:center;font-family:"Arimo",Arial,sans-serif}
  .card{
    width:490px;height:864px;background:var(--card);border-radius:26px;
    display:flex;flex-direction:column;overflow:hidden;
    box-shadow:0 10px 30px rgba(0,0,0,.18);
  }
  .brand{height:284px;display:flex;flex-direction:column;justify-content:center;padding:0 30px}
  .brand-row{display:flex;align-items:center;gap:14px}
  .brand-dot{width:56px;height:56px;border-radius:50%;background:var(--green);flex:none}
  .brand-name{font-family:"Libre Franklin",Arial,sans-serif;font-weight:800;color:var(--green-dark);font-size:34px;line-height:1.05;text-transform:uppercase;white-space:nowrap}
  .tagline{margin-top:12px;padding-left:70px;font-size:14px;color:var(--ink)}
  .rule{height:8px;background:linear-gradient(var(--green-light),var(--green))}
  .contact-band{
    height:356px;background:linear-gradient(180deg,var(--band-edge),var(--band) 30%,var(--band) 70%,var(--band-edge));
    padding:66px 34px 0;
  }
  .person{font-size:35px;font-weight:400;color:var(--green);letter-spacing:.5px}
  .role{margin-top:12px;font-size:22px;color:var(--muted)}
  .contact-list{list-style:none;margin-top:40px;display:flex;flex-direction:column;gap:13px}
  .contact-list li{display:flex;align-items:center;gap:14px;font-size:22px;color:var(--muted);white-space:nowrap}
  .contact-list svg{width:20px;height:20px;flex:none}
  .offer{flex:1;display:flex;flex-direction:column;justify-content:center;padding:0 34px}
  .offer-title{font-family:"Libre Franklin",Arial,sans-serif;font-weight:800;color:var(--green-dark);font-size:47px;line-height:1;white-space:nowrap}
  .offer-sub{margin-top:12px;font-family:"Libre Franklin",Arial,sans-serif;font-weight:800;font-size:23px;color:var(--green-dark);white-space:nowrap}
  .offer-sub span{color:var(--ink)}
</style>
</head>
<body>
  <main class="card">
    <header class="brand">
      <div class="brand-row">
        <span class="brand-dot" aria-hidden="true"></span>
        <span class="brand-name">Steadfast<br>Money Coaching</span>
      </div>
      <p class="tagline">Find a calmer path with your own money</p>
    </header>
    <div class="rule"></div>
    <section class="contact-band">
      <h1 class="person">DANIEL R. HAYES</h1>
      <p class="role">Personal Financial Coach</p>
      <ul class="contact-list">
        <li>
          <svg viewBox="0 0 20 20" aria-hidden="true"><rect x="5" y="1" width="10" height="18" rx="2" fill="none" stroke="var(--green)" stroke-width="2"/><circle cx="10" cy="15.5" r="1.2" fill="var(--green)"/></svg>
          (555) 014-2378
        </li>
        <li>
          <svg viewBox="0 0 20 20" aria-hidden="true"><rect x="1" y="4" width="18" height="12" fill="var(--green)"/><path d="M1 4l9 7 9-7" fill="none" stroke="var(--band)" stroke-width="1.5"/></svg>
          daniel@yourmoneycalm.com
        </li>
        <li>
          <svg viewBox="0 0 20 20" aria-hidden="true"><circle cx="10" cy="10" r="8.5" fill="var(--green)"/><path d="M1.5 10h17M10 1.5c-4 4-4 13 0 17M10 1.5c4 4 4 13 0 17" fill="none" stroke="var(--band)" stroke-width="1.2"/></svg>
          www.yourmoneycalm.com
        </li>
      </ul>
    </section>
    <div class="rule"></div>
    <footer class="offer">
      <p class="offer-title">SPECIAL OFFER!</p>
      <p class="offer-sub"><span>FREE</span> 30 MINUTE CONSULTATION</p>
    </footer>
  </main>
</body>
</html>
```